New Fun, Positive, energised looking Business Card Needed for High Achiever Coach

I am looking for a two sided full colour business card. I am self employed and have recently re branded my 1-2-1 work re-vitalising high achievers. My target client base for these cards is therefore high achievers - usually aged 40 -55, they are often entrepreneurs, CEO or work in banking and finance and 2/3 are male. I work with them on 90 day or 6 month coaching programs to help them live their success in a healthier, more sustainable and fulfiiled way. They pay for this privately so though they are corporate types the cards need not look 'corporate'. I want to portray the idea of transformation, vitality and re-connecting.
You can get a feel for the look I like on my new website: morvenlisk.co.uk
I want to use this logo with strapline (Re-Vitalising High Achievers) (I purchased off Logoharbor) and font/ colours (the turquoise and green).
Details to include on the card:
www.morvenlisk.co.uk
+44 7915 302618
morven@morvenlisk.co.uk
skype: morvenlisk
I'd also like to include:
Do you struggle to switch off? Want to be healthier and feel fitter? Want closer relationships? More clarity over the direction you are headed? I can help you do these things using integrated mind-body techniques. Visit morvenlisk.co.uk TODAY to apply for a FREE Breakthrough session.
BUT if that is too much text for a card I am open to advice/ammendments.
Updates
Thanks for your design - I am considering them. PLease change the wording to :

```html
<!DOCTYPE html>
<html lang="en">
<head>
<meta charset="utf-8">
<title>Morven Lisk – Business Card</title>
<link rel="stylesheet" href="https://fonts.googleapis.com/css2?family=Open+Sans:wght@400;600;700&display=swap">
<style>
  :root {
    --turquoise: #00a7cb;
    --turquoise-deep: #0093b5;
    --green: #5cb96a;
    --ink: #3a3f44;
    --paper: #ffffff;
    --backdrop: #e8e9ed;
    --rule: #d4d6da;
  }
  * { box-sizing: border-box; margin: 0; padding: 0; }
  html, body {
    width: 1200px; height: 987px; overflow: hidden;
    background: var(--backdrop);
    font-family: "Open Sans", Arial, sans-serif;
  }
  .sheet {
    width: 1200px; height: 987px;
    display: flex; flex-direction: column; align-items: center; justify-content: center;
    gap: 40px;
  }
  .card {
    position: relative;
    width: 760px; height: 434px;
    border-radius: 30px;
    overflow: hidden;
    box-shadow: 0 6px 18px rgba(0,0,0,0.12);
  }

  /* Front */
  .card-front { background: var(--paper); }
  .swoosh { position: absolute; inset: 0; width: 100%; height: 100%; }
  .brand {
    position: absolute; left: 70px; top: 70px; width: 300px;
    display: flex; flex-direction: column; align-items: center; gap: 14px;
  }
  .brand-mark {
    width: 78px; height: 78px; border-radius: 50%;
    background: var(--green);
  }
  .brand-name {
    font-weight: 700; font-size: 44px; color: var(--turquoise);
    letter-spacing: 0.5px; line-height: 1;
  }
  .brand-strap {
    font-size: 17px; color: var(--turquoise); font-weight: 400;
    letter-spacing: 0.3px;
  }
  .divider {
    position: absolute; left: 400px; top: 70px; width: 1px; height: 150px;
    background: var(--rule);
  }
  .contacts {
    position: absolute; left: 425px; top: 66px;
    list-style: none; display: flex; flex-direction: column; gap: 12px;
  }
  .contact {
    display: flex; align-items: center; gap: 10px;
    font-size: 20px; color: var(--ink);
  }
  .contact-icon { width: 20px; height: 20px; flex: none; }

  /* Back */
  .card-back { background: var(--turquoise); color: var(--ink); }
  .back-decor {
    position: absolute; left: 300px; top: 60px; width: 300px; height: 300px;
    border-radius: 50%; background: rgba(255,255,255,0.09);
  }
  .questions {
    position: absolute; left: 50px; top: 50px; width: 320px;
    font-size: 17px; line-height: 1.45;
  }
  .answers {
    position: absolute; left: 390px; top: 180px; width: 330px;
    font-size: 17px; line-height: 1.45;
  }
  .label { display: block; font-weight: 600; font-size: 15px; color: #1e2a30; }
  .answers p + p { margin-top: 12px; }
  .highlight { color: var(--paper); font-weight: 700; }
</style>
</head>
<body>
<main class="sheet">

  <section class="card card-front" aria-label="Business card front">
    <svg class="swoosh" viewBox="0 0 760 434" preserveAspectRatio="none" aria-hidden="true">
      <path d="M0 215 C 180 270, 380 360, 560 434 L 0 434 Z" fill="var(--turquoise)"/>
      <path d="M60 224 C 240 300, 420 380, 600 434 L 560 434 C 400 370, 230 300, 40 228 Z" fill="var(--paper)"/>
      <path d="M62 224 C 250 300, 460 390, 760 420 L 760 434 L 600 434 C 420 380, 240 300, 62 224 Z" fill="var(--green)"/>
    </svg>

    <div class="brand">
      <span class="brand-mark" aria-hidden="true"></span>
      <span class="brand-name">Morven Lisk</span>
      <span class="brand-strap">Re-Vitalising High Achievers</span>
    </div>

    <span class="divider" aria-hidden="true"></span>

    <ul class="contacts">
      <li class="contact">
        <svg class="contact-icon" viewBox="0 0 20 20" aria-hidden="true">
          <circle cx="10" cy="10" r="10" fill="var(--turquoise)"/>
          <path d="M7 5 l2 3 -1 1 c1 2 2 3 4 4 l1-1 3 2 -1 2 c-5 0 -9-4 -9-9 z" fill="#fff"/>
        </svg>
        +44 7915 302618
      </li>
      <li class="contact">
        <svg class="contact-icon" viewBox="0 0 20 20" aria-hidden="true">
          <circle cx="10" cy="10" r="10" fill="var(--turquoise)"/>
          <rect x="5" y="6.5" width="10" height="7" fill="#fff"/>
          <path d="M5 6.5 L10 11 L15 6.5" fill="none" stroke="var(--turquoise)" stroke-width="1.2"/>
        </svg>
        morven@morvenlisk.co.uk
      </li>
      <li class="contact">
        <svg class="contact-icon" viewBox="0 0 20 20" aria-hidden="true">
          <circle cx="10" cy="10" r="10" fill="var(--turquoise)"/>
          <circle cx="10" cy="10" r="5.5" fill="none" stroke="#fff" stroke-width="1.3"/>
          <ellipse cx="10" cy="10" rx="2.3" ry="5.5" fill="none" stroke="#fff" stroke-width="1.1"/>
          <line x1="4.5" y1="10" x2="15.5" y2="10" stroke="#fff" stroke-width="1.1"/>
        </svg>
        www.morvenlisk.co.uk
      </li>
      <li class="contact">
        <svg class="contact-icon" viewBox="0 0 20 20" aria-hidden="true">
          <rect width="20" height="20" rx="4" fill="var(--turquoise)"/>
        </svg>
        morvenlisk
      </li>
    </ul>
  </section>

  <section class="card card-back" aria-label="Business card back">
    <span class="back-decor" aria-hidden="true"></span>
    <div class="questions">
      <span class="label">Q</span>
      <p>Do you struggle to switch off?<br>
      Want to be healthier &amp; feel fitter?<br>
      Want closer relationships?<br>
      More clarity over the direction you are headed?</p>
    </div>
    <div class="answers">
      <span class="label">A</span>
      <p>I can help you do these things using integrated mind-body techniques.</p>
      <p>Visit <span class="highlight">morvenlisk.co.uk</span> TODAY to apply for a FREE Breakthrough session.</p>
    </div>
  </section>

</main>
</body>
</html>
```